Label design - Superfood blend

We are a family owned nutrition company with big ambitions. Our goal is to develop a range of 100% natural supplements for women, inspired by nature & modern technology that helps them meet their nutritional needs while nourishing them from within. All our products are junk free because we believe that that’s how nature intended it. We also produce products through a sustainable process and only use biodegradable packaging for our products (See link - https://www.loamwrap.org.uk/biodegradable-stand-pouch-250g-kraft)

Our brand style is modern and minimalist. This same style will be reflected in our social media, website and we want it to be represented through the label designs for our product packaging.

We want some creative designers to design a label that is true to our style (See attached packaging brief with designs we like) and displays our values of Premium, High Quality, Organic Real Food supplements focused on women. I have provided examples in the attached brief, but please only use as inspiration, I dont want any of them to be copied (sorry have had my fingers burnt already !)
Updates

Hello all, Please note this design is for a LABEL and not the whole package. We will have a 500gm biodegradable brown package, and we will have a label (which is what this project is about) that will be stuck on the front. The size of the label will be a rectangle (unless you come up with a new shape) in the size 20cm * 15cm. Please do not submit designs for the WHOLE from of the package, as we dont intend to have printed packages. Regards

Hello all, I have added a new logo version to the attachments, could you please also try that version. Could you also please look at the new sliders. We are only looking for a minimlaist theme. If you dont know what that means, please do feel free to ask, I would be happy to supply examples. Minimalist designs, means clean, modern, upmarket, elegant designs. It does not use too many colors and mostly sticks to a combination of black and white with colors used sparingly. See some below for your reference anyway. https://www.pitchloft.co.uk/design/13359317 https://www.pitchloft.co.uk/design/17270649 https://www.pitchloft.co.uk/design/12584145 https://www.pitchloft.co.uk/design/12367479 https://www.snapquilt.com/search/pins/?q=minimalist%20label%20design&rs=rs&eq=&etslf=2809&term_meta[]=minimalist%7Crecentsearch%7Cundefined&term_meta[]=label%7Crecentsearch%7Cundefined&term_meta[]=design%7Crecentsearch%7Cundefined Regards

Target Market(s)

The target market is women between the age 25 to 45, based in UK (mostly based in larger cities in UK). They are typically middle class or higher and would be in demanding jobs and social lives, that requires for them to meet their nutrition needs in convenient, easy to take forms. The women would also be socially conscious and sensitive to issues like women's rights, environmental issues, healthy food, organic food and sustainability etc. I have a much more detailed customer avatar if required

Font styles to use
Serif
Sans Serif
Decorative
Script

Colors
e8e8e8
474747
1b1b1b
add136

Requirements
Must have
• The label, should look minimalist and modern, throw in some out of the box creativity and we have a winner. Creativity will definitely be of importance. Our packaging is a biodegradable brown paper stand up pouch (Example link in product description). So to make it standout from other colorful packaging - being creative would definitely help.
• Please use the color schemes provided in the brief (See attachments). But if you want to experiment I would be open to it, as long as they are still minimalist and does not stray very far from the color given in the brief :)

```html
<!DOCTYPE html>
<html lang="en">
<head>
<meta charset="utf-8">
<title>Fernhale – Feed The Root label range</title>
<link rel="stylesheet" href="https://fonts.googleapis.com/css2?family=Montserrat:wght@400;500;600;700&display=swap">
<style>
  :root {
    --paper: #ffffff;
    --label: #f3f3f3;
    --label-edge: #e8e8e8;
    --grey: #474747;
    --ink: #1b1b1b;
    --lime: #add136;
    --soft: #9a9a9a;
  }
  * { box-sizing: border-box; margin: 0; padding: 0; }
  html, body { width: 1200px; height: 857px; overflow: hidden; background: var(--paper); }
  body { font-family: "Montserrat", sans-serif; color: var(--ink); position: relative; }

  .label {
    position: absolute; top: 377px; width: 178px; height: 240px;
    background: linear-gradient(180deg, #fafafa 0%, var(--label) 60%, var(--label-edge) 100%);
    border-radius: 6px; overflow: hidden;
    box-shadow: 0 1px 3px rgba(0,0,0,.12);
  }
  .label--one { left: 105px; }
  .label--two { left: 371px; }
  .label--three { left: 638px; }
  .label--four { left: 904px; }

  /* Split layout: pattern strip + stacked text */
  .pattern-strip { position: absolute; top: 0; bottom: 0; width: 64px; }
  .label--one .pattern-strip { left: 0; background: linear-gradient(135deg, var(--lime), var(--grey) 50%, var(--lime)); }
  .label--two .pattern-strip { right: 0; width: 58px; background: linear-gradient(135deg, #b8b8b8, #5a5a5a 50%, #9a9a9a); }

  .brand { font-size: 11.5px; font-weight: 400; letter-spacing: 2.6px; color: var(--ink); white-space: nowrap; }
  .stack { position: absolute; top: 0; width: 100px; }
  .label--one .stack { left: 74px; }
  .label--two .stack { left: 14px; }
  .stack .brand { margin-top: 46px; }
  .title-main { font-size: 27px; font-weight: 700; line-height: 1; margin-top: 16px; letter-spacing: -0.5px; }
  .label--one .title-main { color: var(--grey); }
  .label--two .title-main { color: var(--lime); }
  .title-sub {
    font-size: 15px; font-weight: 600; line-height: 1; margin-top: 2px;
    color: var(--label); -webkit-text-stroke: 0.7px #8a8a8a; letter-spacing: 0.5px;
  }
  .rule { height: 1px; background: var(--soft); margin-top: 6px; width: 84px; }
  .kind { font-size: 7px; font-weight: 600; margin-top: 5px; letter-spacing: 0.2px; white-space: nowrap; }
  .blurb { font-size: 4.6px; line-height: 1.35; margin-top: 16px; color: var(--grey); text-transform: uppercase; }
  .badges { display: flex; gap: 14px; margin-top: 10px; align-items: center; }
  .badge { width: 24px; height: 24px; border-radius: 50%; border: 1px solid var(--soft); }
  .badge--leaf { width: 20px; height: 20px; border-color: var(--lime); }
  .weight { font-size: 7px; color: var(--grey); line-height: 1.5; margin-top: 6px; text-align: center; width: 46px; }
  .weight-tag { position: absolute; right: 8px; bottom: 20px; font-size: 7px; color: var(--label-edge); text-align: center; line-height: 1.4; }

  /* Banded layout */
  .centered { position: absolute; left: 0; right: 0; text-align: center; }
  .label--three .brand, .label--four .brand { position: absolute; left: 0; right: 0; top: 43px; text-align: center; letter-spacing: 3.2px; font-size: 12px; }
  .band { position: absolute; left: 3px; width: 169px; top: 105px; height: 29px; }
  .label--three .band { background: var(--lime); }
  .label--four .band { background: var(--grey); }
  .frame { position: absolute; left: 32px; width: 115px; top: 93px; height: 48px; border: 1px solid var(--ink); }
  .label--four .frame { border-color: var(--lime); }
  .band-title {
    position: absolute; left: 32px; width: 115px; top: 111px;
    text-align: center; font-size: 11.5px; font-weight: 600; line-height: 16px; white-space: nowrap;
  }
  .label--three .band-title { color: var(--ink); }
  .label--four .band-title { color: var(--lime); }
  .frame-kind { position: absolute; left: 0; right: 0; top: 137px; text-align: center; line-height: 8px; }
  .frame-kind span { background: #f1f1f1; padding: 0 4px; font-size: 5.5px; font-weight: 600; }
  .desc { top: 169px; font-size: 5.8px; line-height: 1.45; color: var(--grey); }
  .label--three .badges, .label--four .badges { position: absolute; left: 62px; top: 192px; margin: 0; }
  .base-rule { position: absolute; left: 18px; right: 18px; top: 223px; height: 1px; background: var(--soft); }
  .base-weight { top: 224px; font-size: 4.8px; line-height: 1.3; color: var(--grey); }
</style>
</head>
<body>

<section class="label label--one">
  <div class="pattern-strip" role="img" aria-label="Green and charcoal zigzag pattern strip"></div>
  <div class="stack">
    <p class="brand">FERNHALE</p>
    <h2 class="title-main">FEED</h2>
    <p class="title-sub">THE ROOT</p>
    <div class="rule"></div>
    <p class="kind">FOOD SUPPLEMENT</p>
    <p class="blurb">Organic<br>Plant-based prebiotics<br>and superfood blend</p>
    <div class="badges"><span class="badge"></span><span class="badge badge--leaf"></span></div>
    <p class="weight">Net Weight<br>500 g</p>
  </div>
</section>

<section class="label label--two">
  <div class="pattern-strip" role="img" aria-label="Grey tonal zigzag pattern strip"></div>
  <div class="stack">
    <p class="brand">FERNHALE</p>
    <h2 class="title-main">FEED</h2>
    <p class="title-sub">THE ROOT</p>
    <div class="rule"></div>
    <p class="kind">FOOD SUPPLEMENT</p>
    <p class="blurb">Organic<br>Plant-based prebiotics<br>and superfood blend</p>
    <div class="badges"><span class="badge"></span><span class="badge badge--leaf"></span></div>
  </div>
  <p class="weight-tag">Net Weight<br>500 g</p>
</section>

<section class="label label--three">
  <p class="brand">FERNHALE</p>
  <div class="band"></div>
  <div class="frame"></div>
  <h2 class="band-title">FEED THE ROOT</h2>
  <p class="frame-kind"><span>FOOD SUPPLEMENT</span></p>
  <p class="centered desc">Organic, Plant-Based Prebiotics<br>and Superfood Blend</p>
  <div class="badges"><span class="badge"></span><span class="badge badge--leaf"></span></div>
  <div class="base-rule"></div>
  <p class="centered base-weight">Net Weight<br>500 g</p>
</section>

<section class="label label--four">
  <p class="brand">FERNHALE</p>
  <div class="band"></div>
  <div class="frame"></div>
  <h2 class="band-title">FEED THE ROOT</h2>
  <p class="frame-kind"><span>FOOD SUPPLEMENT</span></p>
  <p class="centered desc">Organic, Plant-Based Prebiotics<br>and Superfood Blend</p>
  <div class="badges"><span class="badge"></span><span class="badge badge--leaf"></span></div>
  <div class="base-rule"></div>
  <p class="centered base-weight">Net Weight<br>500 g</p>
</section>

</body>
</html>
```